Business Card Design

I already have a company logo for my company. I have a logo for the manufacturer we represent. I want a professional business card design.

```html
<!DOCTYPE html>
<html lang="en">
<head>
<meta charset="utf-8">
<title>Beacon Signal LLC — Business Card</title>
<link href="https://fonts.googleapis.com/css2?family=Open+Sans:wght@400;600;700;800&display=swap" rel="stylesheet">
<style>
  :root {
    --backdrop: #232323;
    --card-white: #ffffff;
    --brand-red: #e31e2a;
    --brand-orange: #f07a3a;
    --brand-gold: #c4962a;
    --ink: #1a1a1a;
  }
  * { box-sizing: border-box; margin: 0; padding: 0; }
  html, body {
    width: 1200px; height: 780px; overflow: hidden;
    background: var(--backdrop);
    font-family: "Open Sans", Arial, sans-serif;
  }
  .sheet {
    position: relative; width: 1200px; height: 780px;
    display: flex; align-items: center; justify-content: center; gap: 60px;
  }
  .card {
    position: relative; width: 540px; height: 310px;
    border-radius: 22px; overflow: hidden;
  }
  /* Front */
  .card-front { background: var(--card-white); }
  .front-wave { position: absolute; inset: 0; width: 540px; height: 310px; }
  .brand {
    position: absolute; left: 44px; top: 38px;
    display: flex; align-items: center; gap: 10px;
    color: var(--brand-red); font-weight: 800; font-size: 24px;
    letter-spacing: 0.5px; line-height: 1;
  }
  .brand-mark { width: 16px; height: 16px; background: var(--brand-red); }
  .divider {
    position: absolute; left: 268px; top: 80px;
    width: 1px; height: 136px; background: var(--brand-gold);
  }
  .contact-block { position: absolute; left: 292px; top: 92px; }
  .person-name { font-size: 30px; font-weight: 700; line-height: 1.05; }
  .person-name .first { color: var(--brand-red); }
  .person-name .last { color: var(--brand-gold); }
  .person-role { font-size: 15px; font-weight: 600; color: var(--ink); margin-top: 2px; }
  .contact-list { list-style: none; margin-top: 12px; }
  .contact-list li {
    display: flex; align-items: center; gap: 8px;
    font-size: 14px; color: var(--ink); line-height: 1.55;
  }
  .contact-list svg { width: 12px; height: 12px; flex: none; }
  .address {
    position: absolute; left: 40px; bottom: 18px;
    color: var(--card-white); font-size: 13.5px; font-weight: 400;
  }
  /* Back */
  .card-back {
    background: linear-gradient(115deg, var(--brand-red) 0%, var(--brand-red) 45%, #ea4a32 75%, var(--brand-orange) 100%);
  }
  .back-brand {
    position: absolute; right: 34px; bottom: 28px;
    display: flex; align-items: center; gap: 6px;
    color: var(--card-white); font-weight: 700; font-size: 11px; letter-spacing: 0.5px;
  }
  .back-brand-mark { width: 8px; height: 8px; background: var(--card-white); }
</style>
</head>
<body>
<main class="sheet">
  <section class="card card-front" aria-label="Card front">
    <svg class="front-wave" viewBox="0 0 540 310" aria-hidden="true">
      <path d="M0,92 C90,78 140,120 190,185 C235,240 320,258 540,262 L540,310 L0,310 Z" fill="var(--brand-red)"/>
      <path d="M30,80 C100,72 142,110 186,174 C232,232 320,250 540,253" fill="none" stroke="var(--brand-gold)" stroke-width="6"/>
    </svg>
    <div class="brand"><span class="brand-mark"></span>Beacon Signal LLC</div>
    <div class="divider"></div>
    <div class="contact-block">
      <h1 class="person-name"><span class="first">Daniel</span> <span class="last">Kovar</span></h1>
      <p class="person-role">Managing Director</p>
      <ul class="contact-list">
        <li><svg viewBox="0 0 12 12"><path d="M3 1l2 2.5-1.2 1.2a7 7 0 0 0 3.5 3.5L8.5 7 11 9l-1 2C5 11 1 7 1 2z" fill="var(--brand-red)"/></svg>(555) 014-2290</li>
        <li><svg viewBox="0 0 12 12"><rect x="1" y="2.5" width="10" height="7" rx="1" fill="var(--brand-red)"/><path d="M1.5 3l4.5 3.5L10.5 3" fill="none" stroke="#fff" stroke-width="1"/></svg>hello@beaconsignal.com</li>
        <li><svg viewBox="0 0 12 12"><circle cx="6" cy="6" r="5" fill="var(--brand-red)"/><path d="M1 6h10M6 1c2 2 2 8 0 10M6 1c-2 2-2 8 0 10" fill="none" stroke="#fff" stroke-width="0.8"/></svg>www.beaconsignal.com</li>
      </ul>
    </div>
    <p class="address">418 Maple Ridge Rd. Suite 120 Springfield, TX 75001</p>
  </section>

  <section class="card card-back" role="img" aria-label="Card back: red field with repeating brand pattern fading to orange">
    <div class="back-brand"><span class="back-brand-mark"></span>BEACON SIGNAL</div>
  </section>
</main>
</body>
</html>
```